New Business Card Design Project

Need a design that will create an impact / strong impression towards our clients for our business. We are in the lighting business and we do lighting retrofits for large commercial to industrial clientele.

Target Market(s)

Lighting Industry

Industry/Entity Type

Business

Font styles to use
Other font styles liked:
• we would like to use the font on our logo, not sure what it is though..

Requirements
Must have
• Our logo.
Nice to have
• We are open to suggestions that have to do with lighting.

```html
<!DOCTYPE html>
<html lang="en">
<head>
<meta charset="utf-8">
<title>Brightline Retrofit Group – Business Card</title>
<link href="https://fonts.googleapis.com/css2?family=Arimo:wght@400;700&display=swap" rel="stylesheet">
<style>
  :root {
    --stage: #e9ebea;
    --paper: #ffffff;
    --green-deep: #0f4a22;
    --green-mid: #17803f;
    --green-bright: #5cbf4f;
    --green-band: #1a8a3e;
    --ink: #173f22;
    --rule: #1c3a25;
  }
  * { box-sizing: border-box; margin: 0; padding: 0; }
  html, body {
    width: 1200px; height: 900px; overflow: hidden;
    background: var(--stage);
    font-family: "Arimo", Arial, sans-serif;
  }
  .card {
    position: absolute; left: 250px;
    width: 700px; height: 400px;
    box-shadow: 0 10px 30px rgba(0,0,0,.18);
    overflow: hidden;
  }
  /* back side */
  .card--back {
    top: 30px;
    background: radial-gradient(ellipse at 50% 48%, #1f9a4c 0%, #137036 35%, #0d4d25 70%, #0a3f1e 100%);
    display: flex; align-items: center; justify-content: center;
  }
  .brand {
    display: flex; align-items: center; gap: 12px;
    font-weight: 700; letter-spacing: .02em;
  }
  .brand__mark { width: 16px; height: 16px; }
  .card--back .brand { color: #ffffff; font-size: 30px; }
  .card--back .brand__mark { background: #ffffff; }

  /* front side */
  .card--front {
    top: 470px;
    background: var(--paper);
  }
  .holder { position: absolute; left: 48px; top: 40px; }
  .holder__name { font-weight: 700; font-size: 22px; color: var(--ink); letter-spacing: -.01em; }
  .holder__role { font-size: 15px; color: var(--green-bright); margin-top: 2px; }

  .card--front .brand {
    position: absolute; right: 52px; top: 128px;
    color: var(--green-deep); font-size: 24px;
  }
  .card--front .brand__mark { background: var(--green-mid); }

  .divider {
    position: absolute; left: 48px; right: 48px; top: 210px;
    height: 1.5px; background: var(--rule);
  }
  .contact {
    position: absolute; left: 48px; top: 228px;
    list-style: none; font-size: 16px; color: var(--ink); line-height: 23px;
  }
  .contact li { display: flex; align-items: center; gap: 9px; }
  .contact svg { width: 14px; height: 14px; flex: none; fill: var(--green-bright); }

  .address {
    position: absolute; right: 52px; top: 228px;
    text-align: right; font-size: 17px; color: var(--ink); line-height: 25px;
    font-style: normal;
  }
  .band {
    position: absolute; left: 0; right: 0; bottom: 0;
    height: 22px; background: var(--green-band);
  }
</style>
</head>
<body>

<section class="card card--back" aria-label="Card back">
  <div class="brand"><span class="brand__mark"></span>Brightline Retrofit Group, LLC</div>
</section>

<section class="card card--front" aria-label="Card front">
  <div class="holder">
    <p class="holder__name">YOUR NAME HERE</p>
    <p class="holder__role">MANAGING DIRECTOR</p>
  </div>

  <div class="brand"><span class="brand__mark"></span>Brightline Retrofit Group, LLC</div>

  <div class="divider"></div>

  <ul class="contact">
    <li>
      <svg viewBox="0 0 16 16" aria-hidden="true"><path d="M2 5c0-2 2-3 6-3s6 1 6 3v1h-3V5H5v1H2zM4 7h8l2 6H2z"/></svg>
      41 20 555 0148
    </li>
    <li>
      <svg viewBox="0 0 16 16" aria-hidden="true"><path d="M4 1h8v14H4zM5.5 3v8h5V3z"/></svg>
      41 76 555 2093
    </li>
    <li>
      <svg viewBox="0 0 16 16" aria-hidden="true"><path d="M1 3h14v10H1zM2.5 4.5 8 9l5.5-4.5z"/></svg>
      yourname@brightline.example
    </li>
    <li>
      <svg viewBox="0 0 16 16" aria-hidden="true"><circle cx="8" cy="8" r="7"/><path d="M1 8h14M8 1v14" stroke="#fff" stroke-width="1"/></svg>
      www.brightline.example
    </li>
  </ul>

  <address class="address">
    218 Harlow Avenue, Suite 340<br>
    P.O. Box 48201
  </address>

  <div class="band"></div>
</section>

</body>
</html>
```